Hollendorf Business Card

This is the personal business card for Dr Mark Hollendorf and convers three area of his professional activity - all of them involve (foreign) languages:
o QRVB International Ltd - A translation company with 50 staff. Trades internationally
o WideHarbor Ltd - a global online auction marketplace for translation services (startup)
o Tonal Mosaic - cutting edge technology from the brain sciences which helps learners assimilate the sound patterns of a new language (startup)

Target Market(s)

The card needs to have a "cutting edge" feel - but for a fairly conservative audience - academics, investors.

Industry/Entity Type

Business

Requirements
Must have
• Text:
Dr Mark Hollendorf

Co-founder QRVB International Ltd (Language translation)
Founder WideHarbor Ltd (Translation marketplace)
Founder Tonal Mosaic (Language acquisition)

email: mark.oswin@velmora.co.nz
Phone: +64 21 596 3172
Twitter: @MarkOswin7

```html
<!DOCTYPE html>
<html lang="en">
<head>
<meta charset="utf-8">
<title>Dr Mark Hollendorf – Business Card</title>
<link rel="stylesheet" href="https://fonts.googleapis.com/css2?family=Arimo:wght@400;700&family=Didact+Gothic&display=swap">
<style>
  :root {
    --paper: #ffffff;
    --sage: #9fcc9d;
    --navy: #00007f;
    --ink: #000000;
  }
  html, body {
    margin: 0;
    padding: 0;
    width: 1200px;
    height: 686px;
    overflow: hidden;
    background: var(--paper);
  }
  .business-card {
    display: block;
    width: 1200px;
    height: 686px;
  }
  .card-paper { fill: var(--paper); }
  .sage-panel { fill: var(--sage); }
  .name-band { fill: var(--navy); }
  .contact-field { fill: var(--paper); }

  .header-name {
    font-family: "Arimo", Arial, sans-serif;
    font-weight: 700;
    font-size: 34px;
    fill: var(--ink);
  }
  .header-tagline {
    font-family: "Arimo", Arial, sans-serif;
    font-size: 24px;
    fill: var(--ink);
  }
  .band-name {
    font-family: "Arimo", Arial, sans-serif;
    font-size: 38px;
    letter-spacing: 9px;
    fill: var(--paper);
  }
  .venture-line {
    font-family: "Didact Gothic", "Century Gothic", sans-serif;
    font-size: 17px;
    fill: var(--ink);
  }
  .contact-line {
    font-family: "Arimo", Arial, sans-serif;
    font-size: 30px;
    fill: var(--ink);
  }
</style>
</head>
<body>
<svg class="business-card" viewBox="0 0 1200 686" xmlns="http://www.w3.org/2000/svg" role="img" aria-label="Business card of Dr Mark Hollendorf">
  <rect class="card-paper" x="0" y="0" width="1200" height="686"/>
  <rect class="sage-panel" x="390" y="0" width="810" height="686"/>

  <path class="contact-field" d="M700 344 H1200 V686 H690 C600 660 560 600 560 520 C560 420 610 350 700 344 Z"/>

  <path class="name-band" d="M107 229 H1200 V344 H107 A57.5 57.5 0 0 1 107 229 Z"/>

  <g class="card-header">
    <text class="header-name" x="672" y="112">Mark Hollendorf</text>
    <text class="header-tagline" x="672" y="150">Profession in Foreign Languages</text>
  </g>

  <text class="band-name" x="119" y="309">Dr. Mark Hollendorf</text>

  <g class="ventures">
    <text class="venture-line" x="672" y="400">Co-founder QRVB International Ltd (Language</text>
    <text class="venture-line" x="672" y="423">Translation)</text>
    <text class="venture-line" x="672" y="467">Founder WideHarbor Ltd (Translation Marketplace)</text>
    <text class="venture-line" x="672" y="511">Founder Tonal Mosaic (Language Acquisition)</text>
  </g>

  <g class="contact-details">
    <text class="contact-line" x="672" y="563">Phone: +64 21 596 3172</text>
    <text class="contact-line" x="672" y="604">Twitter: @MarkOswin7</text>
    <text class="contact-line" x="672" y="640">E-mail: mark.oswin@velmora.co.nz</text>
  </g>
</svg>
</body>
</html>
```